Homeowners Insurance Provider Website

We are selling homeowners insurance policy / tenants Policy/Flood Insurance in USA in few states and planning expand nationally.

Our target audience are two folds: Customers (Buy policies) and Insurance Agents who wants to work with us to sell our policies to customers. But website should focus 80% on customers and 20% on agents. So, more customer focused user experience. Please note that there is no direct buy option for customers. They always go through insurance agents.

Customer focused, educational that makes buyer journey easy. We don’t want to come off as trying sell something as there is no direct sales involved from website.

Target Market(s)

Homeowners in USA and Insurance agent who sells these insurance.

Industry/Entity Type

Insurance

Number of Pages Required

4 page

Font styles to use
Other font styles liked:
• Open to suggestions

Colors

Designer to choose colors to be used in the design.

Requirements
Must have
• Three most important things: Trustworthy, Authentic, Simple
• Please use colors form logo and grays
• We like: www.hollowmere.com
• https://www.quillfenbrook.com/
• We need Agent Look up tool on home page similar to what is shown on example sites.
• Design:
• Home Page - Open to Ideas
• Insurance (Products) Landing Page - Info similar to: https://www.quillfenbrook.com/insurance/
• Agents Page - https://www.quillfenbrook.com/agents/
• Claims Page - Information similar to: https://www.quillfenbrook.com/claims-center/
• Site Navigation:
• Home
• Insurance
• Claims
• Agents
• About Us
• Contact Us
Nice to have
• Elegant, minimal and clean design that reflects trust and authenticity.
Should not have
• Slider or rotating images - prefer flat design. Not over powering design.

```html
<!DOCTYPE html>
<html lang="en">
<head>
<meta charset="utf-8">
<title>Hearthbay Insurance Co.</title>
<link rel="stylesheet" href="https://fonts.googleapis.com/css2?family=Lato:wght@400;700;900&display=swap">
<style>
:root{
  --navy:#102b6e;
  --navy-bar:#213b7b;
  --red:#d3202f;
  --ink:#3c3c3c;
  --muted:#666;
  --gray-1:#f2f2f2;
  --gray-2:#e4e4e4;
  --line:#cfcfcf;
  --footer:#333333;
  --white:#fff;
}
*{box-sizing:border-box;margin:0;padding:0}
html,body{width:1200px;height:2521px;overflow:hidden}
body{font-family:'Lato',sans-serif;color:var(--ink);background:var(--white);position:relative}
.abs{position:absolute}

.topbar{left:0;top:0;width:1200px;height:42px;background:var(--navy-bar);color:#fff;font-size:16px}
.topbar .mail{left:77px;top:11px;display:flex;align-items:center;gap:12px}
.topbar .phone{right:82px;top:11px;display:flex;align-items:center;gap:12px}

.header{left:0;top:42px;width:1200px;height:114px;background:#fff}
.brand{left:77px;top:30px;display:flex;align-items:center;gap:14px}
.brand-mark{width:50px;height:50px;background:var(--navy)}
.brand-name{font-size:27px;font-weight:700;color:var(--navy);line-height:1.05;letter-spacing:.5px}
.nav{right:77px;top:36px;display:flex;gap:30px;align-items:center;font-size:17px;color:#444}
.nav a{color:inherit;text-decoration:none;padding:8px 0}
.nav a.active{border:2px solid var(--navy);border-radius:22px;padding:7px 16px;color:var(--navy)}

.hero{left:0;top:156px;width:1200px;height:563px;background:linear-gradient(100deg,#9fb08f 0%,#c8d2c4 25%,#e9e3d6 50%,#d9c7b4 75%,#b8c8d0 100%)}
.hero-badge{left:79px;top:252px;width:364px;height:364px;border-radius:50%;background:var(--navy);color:#fff;text-align:center;padding:108px 38px 0}
.hero-badge h1{font-size:27px;font-weight:400;line-height:1.5;letter-spacing:.5px}
.hero-badge p{font-size:16px;line-height:1.6;margin-top:10px}
.hero-next{left:369px;top:538px;width:57px;height:57px;border-radius:50%;background:#3a3a3a;display:flex;align-items:center;justify-content:center}

.quote{left:810px;top:657px;width:313px;height:447px;background:#fff;box-shadow:0 4px 14px rgba(0,0,0,.15)}
.quote h2{height:62px;background:var(--navy);color:#fff;font-size:27px;font-weight:700;text-align:center;line-height:62px}
.quote .field{margin:0 28px;border-bottom:1px solid var(--line);font-size:14px;color:#888;height:51px;padding-top:22px}
.quote .field.tall{height:94px;padding-top:64px}
.quote .send{display:block;margin:40px auto 0;width:146px;height:50px;border-radius:25px;background:var(--navy);color:#fff;font-size:20px;text-align:center;line-height:50px}

.welcome{left:81px;top:770px;width:660px}
.welcome h2{font-size:32px;font-weight:900;color:var(--navy)}
.welcome h2 span{color:#555;font-weight:700}
.welcome p{font-size:14.5px;line-height:25px;color:#555;margin-top:10px}
.feature{top:930px;width:220px;text-align:left}
.feature .dot{width:62px;height:62px;border-radius:50%;background:var(--red);display:flex;align-items:center;justify-content:center}
.feature span{display:block;font-size:18px;color:#444;margin-top:16px}

.products{left:0;top:1104px;width:1200px;height:521px}
.products .menu{left:0;top:0;width:410px;height:521px;background:var(--gray-1)}
.products .menu h2{position:absolute;left:81px;top:70px;font-size:31px;font-weight:700;color:var(--navy)}
.products .item{position:absolute;left:77px;width:333px;height:73px;border-bottom:1px solid var(--line);display:flex;align-items:center;gap:22px;padding-left:25px;font-size:19px;color:#444;letter-spacing:.3px}
.products .item.active{background:var(--gray-2);border-bottom-color:var(--gray-2)}
.products .detail{left:410px;top:0;width:380px;height:521px;background:var(--gray-2)}
.products .tab{position:absolute;left:24px;top:0;width:72px;height:135px;background:var(--red);border-radius:0 0 36px 36px;display:flex;align-items:flex-end;justify-content:center;padding-bottom:30px}
.products .detail h3{position:absolute;left:123px;top:72px;font-size:21px;font-weight:400;color:#555}
.products .detail p{position:absolute;left:25px;width:340px;font-size:14.5px;line-height:25px;color:#555}
.products .btn{position:absolute;left:25px;top:388px;width:199px;height:51px;border-radius:26px;background:var(--navy);color:#fff;font-size:19px;text-align:center;line-height:51px}
.products .photo{left:790px;top:0;width:410px;height:521px;background:linear-gradient(160deg,#f4f4f2 0%,#ebe8e2 55%,#d9d0c2 100%)}

.faq{left:0;top:1625px;width:1200px}
.faq h2{position:absolute;left:0;width:1200px;top:37px;text-align:center;font-size:32px;font-weight:700;color:var(--navy)}
.acc{position:absolute;left:235px;top:91px;width:728px;border:1px solid var(--line)}
.acc .q{height:46px;background:#eeeeee;border-top:1px solid var(--line);display:flex;align-items:center;gap:12px;padding-left:10px;font-size:18px;color:#444}
.acc .q:first-child{border-top:0}
.acc .a{padding:14px 22px;font-size:14.5px;line-height:25px;color:#555;background:#fff;border-top:1px solid var(--line)}

.cta{left:0;top:2062px;width:1200px;height:126px;background:var(--navy)}
.cta h2{position:absolute;left:79px;top:42px;color:#fff;font-size:32px;font-weight:700}
.cta .btn{position:absolute;left:965px;top:44px;width:156px;height:46px;border-radius:23px;background:#fff;color:var(--navy);font-size:19px;font-weight:700;text-align:center;line-height:46px}

.footer{left:0;top:2188px;width:1200px;height:271px;background:var(--footer);color:#fff}
.footer .brand-f{position:absolute;left:77px;top:58px;display:flex;align-items:center;gap:16px}
.footer .brand-f .sq{width:58px;height:58px;border:3px solid #fff}
.footer .brand-f span{font-size:29px;font-weight:700;line-height:1.05;letter-spacing:.6px}
.footer .subscribe{position:absolute;left:77px;top:160px;width:321px;height:45px;border:1px solid #777;display:flex;align-items:center;justify-content:space-between;padding:0 12px 0 15px;font-size:15px;color:#999}
.footer h3{position:absolute;top:48px;font-size:22px;font-weight:700}
.footer ul{position:absolute;list-style:none;top:96px}
.footer li{display:flex;align-items:center;gap:16px;font-size:15px;height:36.7px}
.contact li{align-items:flex-start;line-height:25px;height:auto;margin-bottom:17px}

.bottombar{left:0;top:2459px;width:1200px;height:62px;background:var(--footer);border-top:1px solid #555;color:#fff}
.bottombar p{position:absolute;left:79px;top:21px;font-size:15px}
.bottombar .social{position:absolute;right:78px;top:9px;display:flex;gap:8px}
.bottombar .social span{width:42px;height:42px;border-radius:50%;background:#fff;display:block}
</style>
</head>
<body>

<div class="abs topbar">
  <div class="abs mail">
    <svg width="18" height="13" viewBox="0 0 18 13"><rect x="1" y="1" width="16" height="11" fill="none" stroke="#fff" stroke-width="1.6"/><path d="M1 1l8 6 8-6" fill="none" stroke="#fff" stroke-width="1.6"/></svg>
    info@hearthbay.com
  </div>
  <div class="abs phone">
    <svg width="17" height="17" viewBox="0 0 24 24"><path fill="#fff" d="M6.6 10.8a15 15 0 006.6 6.6l2.2-2.2c.3-.3.7-.4 1-.2 1.1.4 2.3.6 3.6.6.6 0 1 .4 1 1V20c0 .6-.4 1-1 1A17 17 0 013 4c0-.6.4-1 1-1h3.5c.6 0 1 .4 1 1 0 1.3.2 2.5.6 3.6.1.3 0 .7-.2 1z"/></svg>
    123 456 7890
  </div>
</div>

<header class="abs header">
  <div class="abs brand">
    <span class="brand-mark"></span>
    <span class="brand-name">HEARTHBAY<br>INSURANCE CO.</span>
  </div>
  <nav class="abs nav">
    <a class="active">HOME</a><a>ABOUT</a><a>INSURANCE</a><a>CLAIMS</a><a>AGENTS</a><a>CONTACT</a>
  </nav>
</header>

<section class="abs hero" role="img" aria-label="Smiling family of four sitting together outside their home"></section>
<div class="abs hero-badge">
  <h1>HEARTHBAY<br>INSURANCE CO.</h1>
  <p>Lorem Ipsum is simply dummy text of the printing and typesetting industry. Lorem Ipsum has been.</p>
</div>
<div class="abs hero-next">
  <svg width="24" height="24" viewBox="0 0 24 24"><path d="M4 12h15M13 6l6 6-6 6" fill="none" stroke="#fff" stroke-width="2.4" stroke-linecap="round" stroke-linejoin="round"/></svg>
</div>

<section class="abs welcome">
  <h2>Welcome <span>Visitors!</span></h2>
  <p>Lorem Ipsum is simply dummy text of the printing and typesetting industry. Lorem Ipsum has been the industry's standard dummy text ever since the 1500s, when an unknown printer took a galley of type and scrambled it to make a type specimen book. It has</p>
</section>
<div class="abs feature" style="left:77px">
  <div class="dot"><svg width="34" height="30" viewBox="0 0 34 30"><path d="M17 4L6 13h3v7h16v-7h3z" fill="none" stroke="#fff" stroke-width="2.2" stroke-linejoin="round"/><path d="M2 22c5 0 8 5 15 5s10-5 15-5" fill="none" stroke="#fff" stroke-width="2.2" stroke-linecap="round"/></svg></div>
  <span>homeowners insurance</span>
</div>
<div class="abs feature" style="left:322px">
  <div class="dot"><svg width="34" height="30" viewBox="0 0 34 30"><path d="M6 14L17 5l11 9M10 12v9h14v-9" fill="none" stroke="#fff" stroke-width="2.4" stroke-linejoin="round"/><path d="M4 25h26" stroke="#fff" stroke-width="2.4" stroke-linecap="round"/></svg></div>
  <span>Tenants Policy</span>
</div>
<div class="abs feature" style="left:566px">
  <div class="dot"><svg width="34" height="32" viewBox="0 0 34 32"><path d="M6 14L17 4l11 10M10 12v9h14v-9" fill="none" stroke="#fff" stroke-width="2.2" stroke-linejoin="round"/><rect x="15" y="14" width="4" height="4" fill="#fff"/><path d="M3 25q3.5-3 7 0t7 0 7 0 7 0" fill="none" stroke="#fff" stroke-width="2"/></svg></div>
  <span>Flood Insurance</span>
</div>

<form class="abs quote">
  <h2>Get A Quote</h2>
  <div class="field">Name</div>
  <div class="field">Email</div>
  <div class="field">Phone</div>
  <div class="field tall">Message</div>
  <span class="send">SEND</span>
</form>

<section class="abs products">
  <div class="abs menu">
    <h2>Products</h2>
    <div class="item active" style="top:131px">
      <svg width="26" height="24" viewBox="0 0 26 24"><path d="M13 2L1 12h4v10h6v-6h4v6h6V12h4z" fill="var(--red)"/></svg>Homeowners</div>
    <div class="item" style="top:204px">
      <svg width="26" height="24" viewBox="0 0 26 24"><path d="M2 4h12v19H2zM15 10h9v13h-9z" fill="var(--red)"/><path d="M5 8h2M9 8h2M5 13h2M9 13h2M5 18h2M9 18h2M18 14h3M18 18h3" stroke="#fff" stroke-width="2"/></svg>Renters/Condo</div>
    <div class="item" style="top:277px">
      <svg width="26" height="24" viewBox="0 0 26 24"><path d="M13 3L1 13h4v9h16v-9h4z" fill="var(--red)"/><path d="M13 9c-3 4-3 7 0 9 3-2 3-5 0-9z" fill="#fff"/></svg>Dwelling Fire</div>
    <div class="item" style="top:350px">
      <svg width="26" height="24" viewBox="0 0 26 24"><rect x="3" y="2" width="14" height="19" fill="none" stroke="var(--red)" stroke-width="2"/><path d="M6 7h8M6 11h6M6 15h4" stroke="var(--red)" stroke-width="2"/><circle cx="18" cy="16" r="4" fill="none" stroke="var(--red)" stroke-width="2"/><path d="M21 19l3 3" stroke="var(--red)" stroke-width="2.4"/></svg>Agent Locator Tool</div>
  </div>
  <div class="abs detail">
    <div class="tab"><svg width="38" height="34" viewBox="0 0 26 24"><path d="M13 2L1 12h4v10h6v-6h4v6h6V12h4z" fill="#fff"/></svg></div>
    <h3>Homeowners</h3>
    <p style="top:170px">Lorem Ipsum is simply dummy text of the printing and typesetting industry. Lorem Ipsum has been the industry's standard dummy text ever since the 1500s, when an unknown printer took a galley of type and scrambled.</p>
    <p style="top:307px">Lorem Ipsum is simply dummy text of the printing and typesetting industry.</p>
    <span class="btn">CONTACT NOW</span>
  </div>
  <div class="abs photo" role="img" aria-label="Bright living room with a white sofa, coffee table, flowers and a potted plant"></div>
</section>

<section class="abs faq">
  <h2>FAQs</h2>
  <div class="acc">
    <div class="q"><svg width="16" height="16" viewBox="0 0 16 16"><rect x="1" y="6.5" width="14" height="3" fill="var(--red)"/></svg>Lorem Ipsum is simply dummy text of the printing and typesetting?</div>
    <div class="a">Lorem Ipsum is simply dummy text of the printing and typesetting industry. Lorem Ipsum has been the industry's standard dummy text ever since the 1500s, when an unknown printer took a galley of type and scrambled it to make a type specimen book. It has</div>
    <div class="q"><svg width="16" height="16" viewBox="0 0 16 16"><path d="M1 6.5h14v3H1zM6.5 1h3v14h-3z" fill="var(--red)"/></svg>Lorem Ipsum is simply dummy text of the printing and typesetting?</div>
    <div class="q"><svg width="16" height="16" viewBox="0 0 16 16"><path d="M1 6.5h14v3H1zM6.5 1h3v14h-3z" fill="var(--red)"/></svg>Lorem Ipsum is simply dummy text of the printing and typesetting?</div>
    <div class="q"><svg width="16" height="16" viewBox="0 0 16 16"><path d="M1 6.5h14v3H1zM6.5 1h3v14h-3z" fill="var(--red)"/></svg>Lorem Ipsum is simply dummy text of the printing and typesetting?</div>
  </div>
</section>

<section class="abs cta">
  <h2>Find Your Insurance Agent Now!</h2>
  <span class="btn">FIND NOW</span>
</section>

<footer class="abs footer">
  <div class="brand-f"><span class="sq"></span><span>HEARTHBAY<br>INSURANCE CO.</span></div>
  <div class="subscribe">Email Address
    <svg width="30" height="22" viewBox="0 0 30 22"><path d="M1 10L29 1 20 21l-5-7z" fill="var(--red)"/><path d="M15 14L29 1" stroke="#333" stroke-width="1.5"/></svg>
  </div>
  <h3 style="left:452px">Our Products</h3>
  <ul style="left:452px">
    <li><svg width="14" height="14" viewBox="0 0 14 14"><circle cx="7" cy="7" r="6" fill="none" stroke="var(--red)" stroke-width="1.4"/><path d="M6 4.5L8.5 7 6 9.5" fill="none" stroke="var(--red)" stroke-width="1.4"/></svg>Homeowners</li>
    <li><svg width="14" height="14" viewBox="0 0 14 14"><circle cx="7" cy="7" r="6" fill="none" stroke="var(--red)" stroke-width="1.4"/><path d="M6 4.5L8.5 7 6 9.5" fill="none" stroke="var(--red)" stroke-width="1.4"/></svg>Renters/Condo</li>
    <li><svg width="14" height="14" viewBox="0 0 14 14"><circle cx="7" cy="7" r="6" fill="none" stroke="var(--red)" stroke-width="1.4"/><path d="M6 4.5L8.5 7 6 9.5" fill="none" stroke="var(--red)" stroke-width="1.4"/></svg>Dwelling Fire</li>
    <li><svg width="14" height="14" viewBox="0 0 14 14"><circle cx="7" cy="7" r="6" fill="none" stroke="var(--red)" stroke-width="1.4"/><path d="M6 4.5L8.5 7 6 9.5" fill="none" stroke="var(--red)" stroke-width="1.4"/></svg>Agent Locator Tool</li>
  </ul>
  <h3 style="left:802px">Contact Info</h3>
  <ul class="contact" style="left:802px;width:320px">
    <li><svg width="16" height="22" viewBox="0 0 16 22" style="flex:none;margin-top:2px"><path d="M8 1a7 7 0 00-7 7c0 5 7 13 7 13s7-8 7-13a7 7 0 00-7-7z" fill="var(--red)"/><circle cx="8" cy="8" r="2.6" fill="#333"/></svg>Lorem ipsum dolor sit amet,<br>consectetur adipiscing elit.</li>
    <li><svg width="18" height="18" viewBox="0 0 24 24" style="flex:none;margin-top:3px"><path fill="var(--red)" d="M6.6 10.8a15 15 0 006.6 6.6l2.2-2.2c.3-.3.7-.4 1-.2 1.1.4 2.3.6 3.6.6.6 0 1 .4 1 1V20c0 .6-.4 1-1 1A17 17 0 013 4c0-.6.4-1 1-1h3.5c.6 0 1 .4 1 1 0 1.3.2 2.5.6 3.6.1.3 0 .7-.2 1z"/></svg>123 456 7890</li>
    <li><svg width="18" height="14" viewBox="0 0 18 13" style="flex:none;margin-top:6px"><rect x="1" y="1" width="16" height="11" fill="none" stroke="var(--red)" stroke-width="1.6"/><path d="M1 1l8 6 8-6" fill="none" stroke="var(--red)" stroke-width="1.6"/></svg>info@hearthbay.com</li>
  </ul>
</footer>

<div class="abs bottombar">
  <p>©HEARTHBAY INSURANCE CO. - 2018. All Rights Reserved.</p>
  <div class="social"><span></span><span></span><span></span></div>
</div>

</body>
</html>
```